Design a single page Shopify store web page

We are looking to have a page designed for a single page Shopify store with 2 products. We already have a basic structure that we like, though we are open to suggestions. We are looking for somebody to provide a design/color scheme that we can then implement using Shopify's templating system. We can handle the implementation(HTML / CSS / jS) as we already have 2 web developers on the team, but have not been able to find a design we liked.

The job would consist of providing a mockup (photoshop or otherwise) and any vector graphics you choose to create for the site (we can provide product photos and other images).

You can also look at http://brickdune.com.au for some of our design direction we have used so far

Target Market(s)

Young Australian Males (18 - 49)

Industry/Entity Type

Store

Number of Pages Required

1 page

Font styles to use
Serif
Sans Serif

Requirements
Must have
• Single Page Design
• E-commerce Product Purchase
• Manly (whatever interpretation of that you have)

```html
<!DOCTYPE html>
<html lang="en">
<head>
<meta charset="utf-8">
<title>Brick Dune – Single Page Store</title>
<link href="https://fonts.googleapis.com/css2?family=Arimo:wght@400;700&display=swap" rel="stylesheet">
<style>
:root{
  --black:#000;
  --ink:#0b0b0b;
  --cyan:#00b4f0;
  --cyan-deep:#0397cf;
  --cyan-soft:#b7e6fb;
  --cyan-strip:#2ec2f5;
  --white:#fff;
  --grey:#bdbdbd;
  --card:#f4f4f4;
  --dark-text:#111;
  --bar:#1b1b1b;
}
*{margin:0;padding:0;box-sizing:border-box}
html,body{width:1200px;height:2889px;overflow:hidden}
body{font-family:"Arimo",Arial,sans-serif;background:var(--black);color:var(--white);position:relative}
section,header,footer{position:absolute;left:0;width:1200px}
.abs{position:absolute}

/* nav */
.site-nav{top:0;height:73px;background:var(--black)}
.brand{left:216px;top:30px;font-size:28px;font-weight:700;letter-spacing:1px;color:var(--white);line-height:1}
.nav-link{top:38px;font-size:17px;color:var(--white);line-height:1}
.nav-link.active::after{content:"";position:absolute;left:-17px;right:-17px;top:22px;height:3px;background:var(--cyan)}
.login{left:867px;top:38px;font-size:14px;display:flex;align-items:center;gap:8px;line-height:1}
.login svg{width:18px;height:18px}

/* hero */
.hero{top:73px;height:528px;background:linear-gradient(100deg,#6a4c3a 0%,#b88f6a 30%,#d9c2a6 50%,#8c6a50 72%,#3d2b22 100%)}

/* section headings */
.band-title{font-size:33px;line-height:1;color:var(--white)}
.band-title::after{content:"";position:absolute;left:0;top:44px;width:121px;height:5px;background:var(--cyan)}
.band-title.dark{color:var(--dark-text)}
.band-title.dark::after{background:var(--dark-text)}

/* how it works */
.how-head{top:601px;height:102px;background:var(--black)}
.how-intro{right:216px;top:28px;width:400px;text-align:right;font-size:13px;line-height:16.5px}
.how-body{top:703px;height:358px;background:linear-gradient(180deg,#1d1b19,#2b2622 50%,#171514)}
.step{width:270px;text-align:center;top:41px}
.step-photo{width:156px;height:156px;margin:0 auto;border-radius:50%;border:5px solid var(--cyan);background:radial-gradient(circle,#f2efec,#bdb7b2)}
.step h3{font-weight:400;font-size:19px;color:var(--cyan);margin-top:24px}
.step p{font-size:12.5px;line-height:17px;color:var(--grey);margin-top:10px}

/* plans */
.plans-head{top:1061px;height:95px;background:var(--cyan)}
.perks{left:366px;top:29px;width:616px;height:46px;background:var(--cyan-strip);display:flex;align-items:center;justify-content:space-around;padding:0 6px}
.perk{display:flex;align-items:center;gap:8px;font-size:12.5px;color:var(--white)}
.perk svg{width:20px;height:20px}
.plans-body{top:1156px;height:346px;background:var(--cyan-soft)}
.plan-card{top:32px;width:345px;height:285px;background:var(--card);border-radius:6px;box-shadow:0 4px 10px rgba(0,0,0,.25)}
.plan-ribbon{position:absolute;left:-10px;top:8px;width:361px;height:31px;background:var(--cyan);font-weight:700;font-size:20px;line-height:31px;padding-left:24px}
.plan-photo{position:absolute;left:14px;top:41px;width:140px;height:216px;border:3px solid var(--cyan)}
.plan-info{position:absolute;left:171px;top:58px;width:165px;color:var(--dark-text)}
.plan-info h4{font-size:16px;font-weight:400;margin-bottom:6px}
.plan-info p{font-size:12.5px;line-height:16px;color:#555}
.plan-buy{position:absolute;left:171px;top:233px;display:flex;align-items:center;height:24px}
.price{background:var(--white);color:var(--cyan);font-size:16px;padding:0 10px;height:24px;line-height:24px}
.buy-btn{background:#bfe3f2;color:var(--dark-text);font-size:13px;font-weight:700;height:24px;line-height:24px;padding:0 10px}

/* faq */
.faq-head{top:1502px;height:100px;background:var(--black)}
.faq-body{top:1602px;height:619px;background:linear-gradient(180deg,#1a1816,#24201d 50%,#141312)}
.faq-item{width:260px;text-align:center}
.faq-item h3{font-weight:400;font-size:19px;line-height:24px;color:var(--cyan);margin-bottom:6px}
.faq-item p{font-size:12.5px;line-height:16px;color:#d6d6d6}

/* about */
.about-head{top:2221px;height:96px;background:var(--cyan-deep)}
.about-body{top:2317px;height:318px;background:var(--cyan)}
.about-photo{left:221px;top:33px;width:339px;height:240px;border-radius:10px;border:4px solid #3a3a3a;background:linear-gradient(150deg,#c9c9c9,#6f6f6f 45%,#1d1d1d);box-shadow:0 6px 12px rgba(0,0,0,.45)}
.about-text{left:591px;top:44px;width:393px;font-size:16px;line-height:20.6px}
.read-more{right:216px;top:250px;font-size:20px;color:var(--dark-text);display:flex;align-items:center;gap:8px}
.read-more svg{width:38px;height:16px}

/* footer */
.site-footer{top:2635px;height:188px;background:var(--black)}
.map{left:221px;top:44px;width:182px;height:108px;background:linear-gradient(135deg,#e8e3d4,#cfd8c4 60%,#b9cfe0)}
.foot-col{top:46px;font-size:12.5px;line-height:20px}
.foot-col h5{font-size:14px;font-weight:700;margin-bottom:4px}
.social{display:flex;gap:6px;margin-top:6px}
.social span{width:21px;height:21px;background:#8a8a8a;border-radius:3px}
.bottom-bar{top:2823px;height:66px;background:var(--bar);font-size:11.5px}
.legal{left:220px;top:27px}
.copyright{left:510px;top:27px}
.pay{left:873px;top:20px;display:flex;gap:8px}
.pay span{width:32px;height:22px;background:#e6e6e6;border-radius:3px}
</style>
</head>
<body>

<header class="site-nav">
  <div class="abs brand">BRICK DUNE</div>
  <nav>
    <a class="abs nav-link active" style="left:433px">How it works</a>
    <a class="abs nav-link" style="left:586px">Plans</a>
    <a class="abs nav-link" style="left:680px">FAQ</a>
    <a class="abs nav-link" style="left:765px">About Us</a>
    <span class="abs login"><svg viewBox="0 0 18 18"><circle cx="9" cy="9" r="7" fill="none" stroke="var(--cyan)" stroke-width="2.5"/><path d="M7 9h8" stroke="var(--cyan)" stroke-width="2.5"/></svg>Login/Register</span>
  </nav>
</header>

<section class="hero" role="img" aria-label="Photo of three young men in casual jackets and sunglasses walking through a city street"></section>

<section class="how-head">
  <h2 class="abs band-title" style="left:216px;top:30px">How it works</h2>
  <p class="abs how-intro">Lorem Ipsum is simply dummy text of the printing and typesetting industry. Lorem Ipsum has been the industry's standard dummy text ever since the 1500s</p>
</section>
<section class="how-body" role="img" aria-label="Darkened background photo of young men in a street">
  <div class="abs step" style="left:202px">
    <div class="step-photo" role="img" aria-label="Finger pressing a button"></div>
    <h3>Choose a plan</h3>
    <p>There will be plans for all budgets and<br>styles</p>
  </div>
  <div class="abs step" style="left:464px">
    <div class="step-photo" role="img" aria-label="Young man thinking"></div>
    <h3>Choose how often</h3>
    <p>Descide whether you would like to recieve<br>new packages every 3 or 6 months</p>
  </div>
  <div class="abs step" style="left:730px">
    <div class="step-photo" role="img" aria-label="Gift box with red ribbon"></div>
    <h3>Get your pack</h3>
    <p>We'll send out your first pack right away<br>and then again every 3 or 6 months</p>
  </div>
</section>

<section class="plans-head">
  <h2 class="abs band-title dark" style="left:216px;top:30px">Plans</h2>
  <div class="abs perks">
    <span class="perk"><svg viewBox="0 0 20 20"><path d="M3 10l5 5L17 4" fill="none" stroke="#fff" stroke-width="2.5"/></svg>Free Shipping</span>
    <span class="perk"><svg viewBox="0 0 20 20"><path d="M3 10l5 5L17 4" fill="none" stroke="#fff" stroke-width="2.5"/></svg>Easy Returns</span>
    <span class="perk"><svg viewBox="0 0 20 20"><path d="M3 10l5 5L17 4" fill="none" stroke="#fff" stroke-width="2.5"/></svg>Cancel Whenever</span>
    <span class="perk"><svg viewBox="0 0 20 20"><path d="M3 10l5 5L17 4" fill="none" stroke="#fff" stroke-width="2.5"/></svg>Satisfied Guaranteed</span>
  </div>
</section>
<section class="plans-body">
  <article class="abs plan-card" style="left:233px">
    <div class="plan-ribbon">Comfort</div>
    <div class="plan-photo" role="img" aria-label="Man in a navy suit" style="background:linear-gradient(160deg,#8a5a44,#2b3550 55%,#c9c2b8)"></div>
    <div class="plan-info"><h4>Lorem Ipsum is simply</h4><p>dummy text of the print-<br>ing and typesetting indus-<br>try. Lorem Ipsum has<br>been the industry's stan-<br>dard dummy text ever<br>since the 1500s</p></div>
    <div class="plan-buy"><span class="price">$30</span><span class="buy-btn">GET IT!</span></div>
  </article>
  <article class="abs plan-card" style="left:626px">
    <div class="plan-ribbon">Style</div>
    <div class="plan-photo" role="img" aria-label="Folded patterned sweaters" style="background:linear-gradient(160deg,#3b3e48,#1c2433 55%,#5a4a3a)"></div>
    <div class="plan-info"><h4>Lorem Ipsum is simply</h4><p>dummy text of the print-<br>ing and typesetting indus-<br>try. Lorem Ipsum has<br>been the industry's stan-<br>dard dummy text ever<br>since the 1500s</p></div>
    <div class="plan-buy"><span class="price">$30</span><span class="buy-btn">GET IT!</span></div>
  </article>
</section>

<section class="faq-head">
  <h2 class="abs band-title" style="left:216px;top:30px">FAQ</h2>
</section>
<section class="faq-body" role="img" aria-label="Darkened background photo of a clothing shop">
  <div class="abs faq-item" style="left:207px;top:54px"><h3>What do I get with my<br>Brick Dune plan</h3><p>Lorem Ipsum is simply dummy text of<br>the printing and typesetting industry.<br>Lorem Ipsum has been the industry's<br>standard dummy text ever since the</p></div>
  <div class="abs faq-item" style="left:469px;top:54px"><h3>Return Policy</h3><p>Lorem Ipsum is simply dummy text of<br>the printing and typesetting industry.<br>Lorem Ipsum has been the industry's<br>standard dummy text ever since the</p></div>
  <div class="abs faq-item" style="left:735px;top:54px"><h3>What brands do you<br>stock</h3><p>Lorem Ipsum is simply dummy text of<br>the printing and typesetting industry.<br>Lorem Ipsum has been the industry's<br>standard dummy text ever since the</p></div>
  <div class="abs faq-item" style="left:207px;top:247px"><h3>What is Brick Dune</h3><p>Lorem Ipsum is simply dummy text of<br>the printing and typesetting industry.<br>Lorem Ipsum has been the industry's<br>standard dummy text ever since the</p></div>
  <div class="abs faq-item" style="left:469px;top:247px"><h3>What is your Satisfaction<br>Guarentee</h3><p>Lorem Ipsum is simply dummy text of<br>the printing and typesetting industry.<br>Lorem Ipsum has been the industry's<br>standard dummy text ever since the</p></div>
  <div class="abs faq-item" style="left:735px;top:247px"><h3>Shipping Policy</h3><p>Lorem Ipsum is simply dummy text of<br>the printing and typesetting industry.<br>Lorem Ipsum has been the industry's<br>standard dummy text ever since the</p></div>
  <div class="abs faq-item" style="left:207px;top:436px"><h3>What is your cancellation<br>policy</h3><p>Lorem Ipsum is simply dummy text of<br>the printing and typesetting industry.<br>Lorem Ipsum has been the industry's<br>standard dummy text ever since the</p></div>
  <div class="abs faq-item" style="left:469px;top:436px"><h3>What about sizing</h3><p>Lorem Ipsum is simply dummy text of<br>the printing and typesetting industry.<br>Lorem Ipsum has been the industry's<br>standard dummy text ever since the</p></div>
  <div class="abs faq-item" style="left:735px;top:436px"><h3>How does payment<br>works</h3><p>Lorem Ipsum is simply dummy text of<br>the printing and typesetting industry.<br>Lorem Ipsum has been the industry's<br>standard dummy text ever since the</p></div>
</section>

<section class="about-head">
  <h2 class="abs band-title dark" style="left:216px;top:30px">About Us</h2>
</section>
<section class="about-body">
  <div class="abs about-photo" role="img" aria-label="Photo of printed stickers with the store name"></div>
  <p class="abs about-text">Lorem Ipsum is simply dummy text of the printing and typesetting industry. Lorem Ipsum has been the industry's standard dummy text ever since the 1500s, when an unknown printer took a galley of type and scrambled it to make a type specimen book. It has survived not only five centuries, but also the leap into electronic typesetting, remaining essen-tially unchanged. It was popularised in the 1960s with the release of Letraset sheets containing Lorem</p>
  <a class="abs read-more">Read More <svg viewBox="0 0 38 16"><path d="M2 2l14 6-14 6zM20 2l14 6-14 6z" fill="var(--dark-text)"/></svg></a>
</section>

<footer class="site-footer">
  <div class="abs map" role="img" aria-label="Location map"></div>
  <div class="abs foot-col" style="left:420px">
    <h5>Address</h5>
    <p>Lorem Ipsum is simply dummy text<br>of the printing and type<br>setting industry<br>Phone: +1234567890<br>Email: Lorem Ipsum is simply</p>
  </div>
  <div class="abs foot-col" style="left:674px">
    <h5>Important Links</h5>
    <p>How it works<br>Plans<br>FAQ<br>About US</p>
  </div>
  <div class="abs foot-col" style="left:865px">
    <h5>Fallow Us</h5>
    <div class="social"><span></span><span></span><span></span><span></span></div>
  </div>
</footer>
<div class="abs bottom-bar" style="left:0;width:1200px">
  <span class="abs legal">Site Map &nbsp;|&nbsp; Privacy &nbsp;|&nbsp; Site Credits</span>
  <span class="abs copyright">All Rights Reserved@ 2014 hello@brickdune.com.au</span>
  <div class="abs pay"><span></span><span></span><span></span></div>
</div>

</body>
</html>
```